Liron Vasek Website

Website for my son who is in 7th grade in the US. This will prepare him to show people his accomplishments when applying for a job or going to college. It should have:
* A picture (or multiple pictures)
* A resume page
* A place to share your accomplishments
* Links to his other social profiles
* A contact form

Great to include:
* Internships (show some photos of it along with what you’ve learned).
* Volunteer work.
* A side hustle that you want to highlight

Website sample I like:
https://belinamorud.sitefolio-demo.com/belinamorudtavik

Target Market(s)

For jobs and colleges admissions.

Number of Pages Required

5+ page

Colors

Designer to choose colors to be used in the design.

Requirements
Must have
• * A picture (or multiple pictures)
• * A resume page
• * A place to share your accomplishments
• * Links to his other social profiles
• * A contact form
Nice to have
• Great to include:
• * Internships (show some photos of it along with what you’ve learned).
• * Volunteer work.
• * A side hustle that you want to highlight

```html
<!DOCTYPE html>
<html lang="en">
<head>
<meta charset="utf-8">
<title>Liron Vasek</title>
<link href="https://fonts.googleapis.com/css2?family=Tenor+Sans&family=Lato:wght@400;700&display=swap" rel="stylesheet">
<style>
:root{
  --brand:#0b5e87;
  --brand-deep:#074d70;
  --brand-light:#1a86b8;
  --ink:#1d1d1d;
  --text:#555;
  --white:#fff;
  --footer:#161616;
  --contact-bg:#e4effa;
  --field-border:#e6e6e6;
}
*{margin:0;padding:0;box-sizing:border-box}
html,body{width:1200px;height:4195px;overflow:hidden}
body{position:relative;background:var(--white);font-family:"Lato",sans-serif;color:var(--text)}
.abs{position:absolute}
.heading{font-family:"Tenor Sans",sans-serif;font-weight:400;color:var(--ink)}

/* top bar */
.topbar{left:0;top:0;width:1200px;height:46px;background:var(--brand);color:var(--white);font-size:15px}
.topbar span{position:absolute;top:14px;display:flex;align-items:center;gap:10px}
.topbar svg{width:15px;height:15px;fill:var(--white)}

/* nav */
.nav{left:0;top:46px;width:1200px;height:94px;background:var(--white)}
.logo{position:absolute;left:88px;top:24px;font-family:"Tenor Sans",sans-serif;font-size:40px;color:var(--brand)}
.menu{position:absolute;right:88px;top:40px;display:flex;gap:36px;font-size:15px;color:var(--ink);letter-spacing:.3px}

/* hero */
.hero{left:0;top:140px;width:1200px;height:630px}
.hero-title{left:0;top:290px;width:1200px;text-align:center;font-size:118px;color:var(--white);font-family:"Tenor Sans",sans-serif}
.dots{left:0;top:659px;width:1200px;display:flex;justify-content:center;gap:16px}
.dots i{width:19px;height:19px;border:2px solid var(--white);border-radius:50%}
.dots i.on{background:var(--white)}

/* about */
.about-title{left:0;top:858px;width:1200px;text-align:center;font-size:50px}
.about-text{left:120px;top:936px;width:960px;text-align:center;font-size:15px;line-height:30px}
.btn-solid{left:505px;top:1094px;width:190px;height:48px;border-radius:24px;background:var(--brand);color:var(--white);font-size:17px;font-weight:700;display:flex;align-items:center;justify-content:center;gap:10px}

/* hex cards */
.card{top:1258px;width:317px;height:492px}
.card svg{position:absolute;left:0;top:0}
.card-title{position:absolute;left:0;top:343px;width:317px;text-align:center;font-family:"Tenor Sans",sans-serif;font-size:22px;color:var(--white)}
.card-text{position:absolute;left:60px;top:382px;width:197px;text-align:center;font-size:15px;line-height:23px;color:var(--white)}
.card-link{position:absolute;left:0;top:442px;width:317px;text-align:center;font-size:13px;font-weight:700;color:var(--white)}

/* volunteer */
.volunteer{left:0;top:1864px;width:1200px;height:602px}
.vol-title{left:604px;top:1935px;font-size:50px;color:var(--white)}
.vol-text{left:604px;top:2007px;width:489px;text-align:justify;font-size:15px;line-height:30.4px;color:var(--white)}
.vol-text p+p{margin-top:15px}
.btn-outline{left:604px;top:2328px;width:182px;height:54px;border:2px solid var(--white);border-radius:27px;color:var(--white);font-size:16px;font-weight:700;display:flex;align-items:center;justify-content:center}

/* testimonials */
.test-title{left:0;top:2552px;width:1200px;text-align:center;font-size:50px}
.avatar{left:544px;top:2652px;width:110px;height:110px;border-radius:50%;border:3px solid #ddd;background:radial-gradient(circle at 50% 45%,#e9c9a8,#b78a5c)}
.quote-mark{left:490px;top:2660px;font-family:Georgia,serif;font-size:320px;line-height:1;color:#ececec}
.test-text{left:170px;top:2786px;width:860px;text-align:center;font-size:15px;line-height:28px;color:#333}
.test-name{left:0;top:2861px;width:1200px;text-align:center;font-size:14px;font-weight:700;letter-spacing:1px;color:#444}
.tdots{left:0;top:2925px;width:1200px;display:flex;justify-content:center;gap:12px}
.tdots i{width:9px;height:9px;border-radius:50%;background:#ccc}
.tdots i.on{background:var(--brand-light)}

/* contact */
.contact{left:0;top:3044px;width:1200px;height:1151px;background:linear-gradient(180deg,#e6f1fb 0%,#dbe7f1 45%,#c9d6df 75%,#b9c7cf 100%)}
.contact-title{left:0;top:3128px;width:1200px;text-align:center;font-size:50px}
.field{background:var(--white);border:1px solid var(--field-border);font-size:15px;color:#777;padding:20px 20px}
.btn-submit{left:513px;top:3569px;width:174px;height:55px;border-radius:28px;background:var(--brand);color:var(--white);font-size:17px;font-weight:700;display:flex;align-items:center;justify-content:center}

/* footer */
.footer{left:0;top:3730px;width:1200px;height:465px}
.foot-menu{left:0;top:3903px;width:1200px;display:flex;justify-content:center;gap:40px;font-size:14px;color:#ddd}
.foot-icon{width:56px;height:56px;border-radius:50%;background:#3a3a3a;display:flex;align-items:center;justify-content:center}
.foot-icon.on{background:var(--brand-light)}
.foot-icon svg{width:26px;height:26px;fill:none;stroke:#e6e6e6;stroke-width:1.8}
.foot-info{top:4040px;width:260px;text-align:center;font-size:13px;line-height:24px;color:#ddd}
.foot-rule{left:88px;top:4135px;width:1024px;height:1px;background:#333}
.copy{left:88px;top:4158px;font-size:13px;color:#ccc}
.social{left:930px;top:4156px;display:flex;gap:18px}
.social i{width:16px;height:16px;border-radius:50%;background:#e6e6e6}
</style>
</head>
<body>

<div class="abs topbar">
  <span style="left:90px"><svg viewBox="0 0 24 24"><path d="M6.6 10.8a15 15 0 0 0 6.6 6.6l2.2-2.2c.3-.3.7-.4 1-.2 1.1.4 2.3.6 3.6.6.6 0 1 .4 1 1V20c0 .6-.4 1-1 1A17 17 0 0 1 3 4c0-.6.4-1 1-1h3.5c.6 0 1 .4 1 1 0 1.3.2 2.5.6 3.6.1.3 0 .7-.2 1z"/></svg>555-302-8841</span>
  <span style="left:290px"><svg viewBox="0 0 24 24"><path d="M2 5h20v14H2z M2 5l10 8 10-8" stroke="#0b5e87" stroke-width="1.5"/></svg>hello@lironvasek.example</span>
  <span style="left:770px"><svg viewBox="0 0 24 24"><path d="M12 2a7 7 0 0 0-7 7c0 5 7 13 7 13s7-8 7-13a7 7 0 0 0-7-7zm0 9.5A2.5 2.5 0 1 1 12 6.5a2.5 2.5 0 0 1 0 5z"/></svg>42 Harbor Lane, Westfield, OH 44102, US</span>
</div>

<header class="abs nav">
  <div class="logo"><span style="color:var(--ink)">Liron</span> Vasek</div>
  <nav class="menu"><span>HOME</span><span>PORTFOLIO</span><span>RESUME</span><span>ACHIEVEMENTS</span><span>BLOG</span><span>CONTACT</span></nav>
</header>

<section class="abs hero">
  <svg width="1200" height="630" viewBox="0 0 1200 630">
    <defs>
      <linearGradient id="sky" x1="0" y1="0" x2="0" y2="1">
        <stop offset="0" stop-color="#2f7fc4"/>
        <stop offset="0.55" stop-color="#8fc0e6"/>
        <stop offset="0.72" stop-color="#a3a6a4"/>
        <stop offset="0.82" stop-color="#3f7ea6"/>
        <stop offset="1" stop-color="#14577f"/>
      </linearGradient>
    </defs>
    <rect width="1200" height="630" fill="url(#sky)" role="img" aria-label="City skyline across the river under a blue sky"/>
    <path d="M0 488 Q380 500 600 622 Q820 500 1200 488 L1200 630 L0 630 Z" fill="#fff"/>
    <path d="M0 488 Q380 500 600 622 Q820 500 1200 488" fill="none" stroke="#0b5e87" stroke-width="5"/>
  </svg>
</section>
<div class="abs hero-title">Liron Vasek</div>
<div class="abs dots"><i class="on"></i><i></i><i></i><i></i></div>

<h2 class="abs heading about-title">About Me</h2>
<p class="abs about-text">Lorem ipsum dolor sit amet, consectetur adipiscing elit, sed do eiusmod tempor incididunt ut labore et dolore magna aliqua.<br>Ut enim ad minim veniam, quis nostrud exercitation ullamco laboris nisi ut aliquip ex ea commodo consequat. Duis aute irure dolor in reprehenderit in voluptate velit esse cillum dolore eu fugiat nulla pariatur. Excepteur sint occaecat cupidatat non proident, sunt in culpa qui officia deserunt mollit anim id est laborum.</p>
<div class="abs btn-solid">Read More <svg width="17" height="17" viewBox="0 0 24 24"><circle cx="12" cy="12" r="11" fill="#fff"/><path d="M7 12h9M12 7l5 5-5 5" stroke="#0b5e87" stroke-width="2.6" fill="none"/></svg></div>

<div class="abs card" style="left:90px">
  <svg width="317" height="492" viewBox="0 0 317 492">
    <defs><linearGradient id="blueA" x1="0" y1="0" x2="0" y2="1"><stop offset="0" stop-color="#1a86b8"/><stop offset="1" stop-color="#0b5e87"/></linearGradient></defs>
    <path d="M0 205 L18 215 L18 250 L158 330 L299 250 L299 215 L317 205 L317 400 L158 492 L0 400 Z" fill="url(#blueA)"/>
    <path d="M158 0 L299 80 L299 250 L158 330 L18 250 L18 80 Z" fill="#cfd8de" stroke="#fff" stroke-width="5" role="img" aria-label="Student at a desk explaining his work"/>
  </svg>
  <div class="card-title">A resume page</div>
  <div class="card-text">Sed ut perspiciatis unde omnis iste natus</div>
  <div class="card-link">READ MORE</div>
</div>
<div class="abs card" style="left:441px">
  <svg width="317" height="492" viewBox="0 0 317 492">
    <path d="M0 205 L18 215 L18 250 L158 330 L299 250 L299 215 L317 205 L317 400 L158 492 L0 400 Z" fill="url(#blueA)"/>
    <path d="M158 0 L299 80 L299 250 L158 330 L18 250 L18 80 Z" fill="#b9c4c9" stroke="#fff" stroke-width="5" role="img" aria-label="Student working on a laptop in a lab"/>
  </svg>
  <div class="card-title">Accomplishments</div>
  <div class="card-text">Sed ut perspiciatis unde omnis iste natus</div>
  <div class="card-link">READ MORE</div>
</div>
<div class="abs card" style="left:791px">
  <svg width="317" height="492" viewBox="0 0 317 492">
    <path d="M0 205 L18 215 L18 250 L158 330 L299 250 L299 215 L317 205 L317 400 L158 492 L0 400 Z" fill="url(#blueA)"/>
    <path d="M158 0 L299 80 L299 250 L158 330 L18 250 L18 80 Z" fill="#c8b8b4" stroke="#fff" stroke-width="5" role="img" aria-label="Student and mentor working on an engineering project"/>
  </svg>
  <div class="card-title">Internships</div>
  <div class="card-text">Sed ut perspiciatis unde omnis iste natus</div>
  <div class="card-link">READ MORE</div>
</div>

<section class="abs volunteer">
  <svg width="1200" height="602" viewBox="0 0 1200 602">
    <defs>
      <linearGradient id="volBlue" x1="0" y1="0" x2="1" y2="1"><stop offset="0" stop-color="#0a5a82"/><stop offset="1" stop-color="#0d6a98"/></linearGradient>
      <linearGradient id="volPhoto" x1="0" y1="0" x2="1" y2="1"><stop offset="0" stop-color="#8a7448"/><stop offset="0.5" stop-color="#5a5550"/><stop offset="1" stop-color="#3a342e"/></linearGradient>
    </defs>
    <rect width="1200" height="602" fill="url(#volBlue)"/>
    <path d="M0 0 L468 0 Q520 160 552 300 Q520 440 455 602 L0 602 Z" fill="url(#volPhoto)" role="img" aria-label="Volunteer picking up litter on a sunlit path"/>
    <path d="M468 0 Q520 160 552 300 Q520 440 455 602" fill="none" stroke="#fff" stroke-width="4"/>
  </svg>
</section>
<h2 class="abs heading vol-title">Volunteer work</h2>
<div class="abs vol-text">
  <p>Lorem ipsum dolor sit amet, consectetur adipiscing elit, sed do eiusmod tempor incididunt ut labore et dolore magna aliqua. Ut enim ad minim veniam, quis nostrud exercitation ullamco laboris nisi ut aliquip ex ea commodo consequat. Duis aute irure dolor in derit in voluptate velit esse cillum dolore eu fugiat nulla pariatur. Excepteur sint occaecat cupidatat non proident, sunt in culpa qui officia deserunt mollit anim id est laborum</p>
  <p>Excepteur sint occaecat cupidatat non proident, sunt in culpa qui officia deserunt mollit anim id est laborum</p>
</div>
<div class="abs btn-outline">LEARN MORE</div>

<h2 class="abs heading test-title">Testimonials</h2>
<div class="abs quote-mark">&ldquo;</div>
<div class="abs avatar" role="img" aria-label="Portrait of the reviewer"></div>
<p class="abs test-text">Lorem ipsum dolor sit amet, consectetur adipiscing elit, sed do eiusmod tempor incididunt ut labore et dolore magna aliqua. Ut enim ad minim veniam, quis nostrud exercitation ullamco laboris nisi ut aliquip ex ea commodo consequat</p>
<div class="abs test-name">–MAYA CASTELL</div>
<div class="abs tdots"><i class="on"></i><i></i><i></i></div>

<section class="abs contact" role="img" aria-label="Faded city skyline background"></section>
<h2 class="abs heading contact-title">Contact Us</h2>
<div class="abs field" style="left:103px;top:3227px;width:483px;height:60px">Name</div>
<div class="abs field" style="left:612px;top:3227px;width:484px;height:60px">Email</div>
<div class="abs field" style="left:103px;top:3313px;width:483px;height:60px">Phone</div>
<div class="abs field" style="left:612px;top:3313px;width:484px;height:60px">Subject</div>
<div class="abs field" style="left:103px;top:3400px;width:993px;height:141px">Message</div>
<div class="abs btn-submit">SUBMIT</div>

<footer class="abs footer">
  <svg width="1200" height="465" viewBox="0 0 1200 465">
    <path d="M0 136 Q380 120 600 7 Q820 120 1200 136 L1200 465 L0 465 Z" fill="var(--footer)"/>
    <path d="M0 136 Q380 120 600 7 Q820 120 1200 136" fill="none" stroke="#0b5e87" stroke-width="5"/>
  </svg>
</footer>
<nav class="abs foot-menu"><span>HOME</span><span>PORTFOLIO</span><span>RESUME</span><span>ACHIEVEMENTS</span><span>BLOG</span><span>CONTACT</span></nav>
<div class="abs foot-icon" style="left:285px;top:3966px"><svg viewBox="0 0 24 24"><path d="M12 2a7 7 0 0 0-7 7c0 5 7 13 7 13s7-8 7-13a7 7 0 0 0-7-7z"/><circle cx="12" cy="9" r="2.5"/></svg></div>
<div class="abs foot-icon on" style="left:570px;top:3966px"><svg viewBox="0 0 24 24"><path d="M6.6 10.8a15 15 0 0 0 6.6 6.6l2.2-2.2c.3-.3.7-.4 1-.2 1.1.4 2.3.6 3.6.6.6 0 1 .4 1 1V20c0 .6-.4 1-1 1A17 17 0 0 1 3 4c0-.6.4-1 1-1h3.5c.6 0 1 .4 1 1 0 1.3.2 2.5.6 3.6.1.3 0 .7-.2 1z"/></svg></div>
<div class="abs foot-icon" style="left:858px;top:3966px"><svg viewBox="0 0 24 24"><rect x="3" y="6" width="18" height="12"/><path d="M3 6l9 7 9-7"/></svg></div>
<div class="abs foot-info" style="left:183px">42 Harbor Lane<br>Westfield, OH 44102, US</div>
<div class="abs foot-info" style="left:468px">555-214-7730</div>
<div class="abs foot-info" style="left:756px">hello@lironvasek.example</div>
<div class="abs foot-rule"></div>
<div class="abs copy">© 2019 Copyrights Vasek Studio. All Rights Reserved</div>
<div class="abs social"><i></i><i></i><i></i><i></i><i></i></div>

</body>
</html>
```